New travel store signage for Marlow Journeys to attract luxury travellers.

Hello,
We are looking to change the signage of our stores. The signage must include the following:
1. Marlow Journeys Logo (attached)
2. The text...The Travel & Cruise Experts
3. Brand Colours ( Fb0196, 412266, d41d84 and ffffff)
Please note the signage design must be central and only cover two thirds of the store front. We have also attached an image of one of our new stores which might be helpful when preparing a mock up.

We are looking for a quick turnaround on this, making a decision within 48 hours.

Target Market(s)

Retail

Industry/Entity Type

Travel Agency

Font styles to use
Other font styles liked:
• Radley

Colors
E54698
E96AAD
F1A4CE
F9D9EA
FCEFF6
6B429C
8869AF
B7A5CE
E3DAEB
F3F0F8

Requirements
Must have
• Hello, We are looking to change the signage of our stores. The signage must include the following: 1. Marlow Journeys Logo (attached) 2. The text...The Travel & Cruise Experts 3. Brand Colours ( Fb0196, 412266, d41d84 and ffffff) Please note the signage design must be central and only cover two thirds of the store front.
Should not have
• different colour or fonts. Gradient design.

```html
<!DOCTYPE html>
<html lang="en">
<head>
<meta charset="utf-8">
<title>Marlow Journeys – Store Signage</title>
<link rel="stylesheet" href="https://fonts.googleapis.com/css2?family=Radley&display=swap">
<style>
  :root {
    --brand-purple: #412266;
    --brand-pink: #fb0196;
    --brand-rose: #d41d84;
    --brand-white: #ffffff;
    --backdrop: #eceaef;
  }
  html, body {
    margin: 0;
    padding: 0;
    overflow: hidden;
  }
  body {
    width: 1200px;
    height: 1117px;
    background: var(--backdrop);
    font-family: "Radley", Georgia, serif;
    position: relative;
  }
  .signage {
    position: absolute;
    left: 50px;
    width: 1100px;
    display: block;
    box-shadow: 0 6px 18px rgba(65, 34, 102, 0.18);
  }
  .signage--fascia { top: 200px; }
  .signage--corner { top: 600px; }
  .sign-text { font-family: "Radley", Georgia, serif; }
  .tagline { fill: var(--brand-white); }
  .brand-name { fill: var(--brand-purple); }
  .fold-line { stroke: rgba(0, 0, 0, 0.22); stroke-width: 2; }
</style>
</head>
<body>

  <svg class="signage signage--fascia" viewBox="0 0 1390 165" height="131" role="img" aria-label="Marlow Journeys fascia sign: The Travel &amp; Cruise Experts">
    <rect class="panel-purple" width="1390" height="165" fill="var(--brand-purple)"/>
    <rect class="panel-white" width="540" height="135" fill="var(--brand-white)"/>
    <rect class="accent-band" y="135" width="1390" height="30" fill="var(--brand-pink)" role="img" aria-label="Decorative brand band"/>
    <g class="brand-mark">
      <circle cx="150" cy="68" r="12" fill="var(--brand-rose)"/>
      <text class="sign-text brand-name" x="172" y="78" font-size="30">Marlow Journeys</text>
    </g>
    <text class="sign-text tagline" x="590" y="62" font-size="56">The Travel &amp;</text>
    <text class="sign-text tagline" x="590" y="118" font-size="56">Cruise Experts</text>
  </svg>

  <svg class="signage signage--corner" viewBox="0 0 1390 190" height="150" role="img" aria-label="Marlow Journeys corner sign: The Travel &amp; Cruise Experts, with arrow pointing left">
    <rect class="panel-purple" width="1390" height="190" fill="var(--brand-purple)"/>
    <rect class="panel-white" width="250" height="155" fill="var(--brand-white)"/>
    <rect class="accent-band" y="155" width="1390" height="35" fill="var(--brand-pink)" role="img" aria-label="Decorative brand band"/>
    <line class="fold-line" x1="1000" y1="0" x2="1000" y2="190"/>
    <g class="brand-mark">
      <circle cx="26" cy="80" r="9" fill="var(--brand-rose)"/>
      <text class="sign-text brand-name" x="42" y="88" font-size="22">Marlow Journeys</text>
    </g>
    <text class="sign-text tagline" x="290" y="72" font-size="54">The Travel &amp;</text>
    <text class="sign-text tagline" x="290" y="128" font-size="54">Cruise Experts</text>
    <path class="direction-arrow" d="M1110,78 L1170,38 V63 H1280 V93 H1170 V118 Z" fill="var(--brand-white)"/>
  </svg>

</body>
</html>
```